Marlo clean Business Cards

I'm looking for someone to design my business card using my company name and logo. I would like it it be clean, fresh and a little out of the box. The colors I would like used are the same two in my logo (gold and the teal blue color) I also want it to screen high end scene the company name is Marlo clean :) I'm a commercial cleaning company based out of Orange and San Diego county. Once I receive your email I will send over the file. Because the file is quote big with several options of logos. Please be an out of the box thinker and take some risk...I'm looking for someone to put themselves out there. Thanks and good luck

```html
<!DOCTYPE html>
<html lang="en">
<head>
<meta charset="utf-8">
<title>Marlo clean – Business Cards</title>
<link href="https://fonts.googleapis.com/css2?family=Exo+2:wght@400;500;600&display=swap" rel="stylesheet">
<style>
  :root {
    --bg: #2b2b2d;
    --card-light: #f4f4f4;
    --card-light-edge: #d9d9da;
    --card-dark: #3a3a3b;
    --ink: #2f2f31;
    --ink-soft: #4a4a4c;
    --accent: #2f8fc4;
    --on-dark: #f2f2f2;
  }
  * { box-sizing: border-box; margin: 0; padding: 0; }
  html, body { width: 1200px; height: 870px; overflow: hidden; }
  body {
    background: var(--bg);
    font-family: "Exo 2", "Trebuchet MS", sans-serif;
    position: relative;
  }
  .card {
    position: absolute;
    width: 640px;
    height: 366px;
    border-radius: 3px;
    overflow: hidden;
    box-shadow: 0 12px 30px rgba(0,0,0,.45);
  }
  .card--front {
    left: 70px; top: 55px;
    background: linear-gradient(120deg, var(--card-light) 0%, #ffffff 45%, var(--card-light-edge) 100%);
    display: flex; align-items: center; justify-content: center;
  }
  .card--back {
    left: 490px; top: 450px;
    background: var(--card-dark);
  }
  .brand {
    display: flex; align-items: center; gap: 18px;
  }
  .brand__dot {
    width: 54px; height: 54px; border-radius: 50%;
    background: var(--accent);
    flex: none;
  }
  .brand__name {
    font-weight: 600;
    text-transform: uppercase;
    letter-spacing: 4px;
    color: var(--ink);
    font-size: 38px;
  }
  .back__top {
    position: absolute; left: 0; top: 0;
    width: 100%; height: 212px;
    background: linear-gradient(120deg, #e6e6e7 0%, #ffffff 50%, var(--card-light-edge) 100%);
  }
  .contacts {
    position: absolute; left: 34px; top: 26px;
    list-style: none;
  }
  .contacts li {
    display: flex; align-items: center; gap: 10px;
    font-size: 13px; color: var(--ink-soft);
    height: 31px;
  }
  .contacts svg { width: 14px; height: 14px; fill: var(--accent); flex: none; }
  .back__brand {
    position: absolute; right: 40px; top: 82px;
  }
  .back__brand .brand__dot { width: 46px; height: 46px; }
  .back__brand .brand__name { font-size: 30px; letter-spacing: 3px; }
  .address {
    position: absolute; left: 34px; top: 238px;
    color: var(--on-dark);
    font-size: 16px; line-height: 1.5;
  }
  .person {
    position: absolute; right: 40px; bottom: 36px;
    text-align: right; color: var(--on-dark);
  }
  .person__name { font-size: 19px; font-weight: 500; letter-spacing: 1px; text-transform: uppercase; }
  .person__title { font-size: 14px; margin-top: 2px; }
</style>
</head>
<body>

<section class="card card--front" aria-label="Card front">
  <div class="brand">
    <span class="brand__dot"></span>
    <span class="brand__name">Marlo clean</span>
  </div>
</section>

<section class="card card--back" aria-label="Card back">
  <div class="back__top">
    <ul class="contacts">
      <li><svg viewBox="0 0 16 16"><path d="M3 1h3l1 4-2 1a9 9 0 0 0 5 5l1-2 4 1v3a2 2 0 0 1-2 2A13 13 0 0 1 1 3a2 2 0 0 1 2-2z"/></svg>014 552 3170</li>
      <li><svg viewBox="0 0 16 16"><path d="M4 0h8a1 1 0 0 1 1 1v14a1 1 0 0 1-1 1H4a1 1 0 0 1-1-1V1a1 1 0 0 1 1-1zm1 2v10h6V2zm3 11a1 1 0 1 0 0 2 1 1 0 0 0 0-2z"/></svg>014 552 3171</li>
      <li><svg viewBox="0 0 16 16"><path d="M4 0h6l3 3v3h2v9H1V6h3zm1 1v5h7V3.5L9.5 1zM3 9v2h2V9zm4 0v2h2V9zm4 0v2h2V9z"/></svg>014 552 3172</li>
      <li><svg viewBox="0 0 16 16"><path d="M0 3h16v10H0zm1.5 1.2L8 9l6.5-4.8V4h-13z"/></svg>hello@marloclean.com</li>
      <li><svg viewBox="0 0 16 16"><path d="M8 0a8 8 0 1 0 0 16A8 8 0 0 0 8 0zm0 1.5c1 1.2 1.7 3 1.9 5.5H6.1C6.3 4.5 7 2.7 8 1.5zM1.6 7a6.5 6.5 0 0 1 3-4.9A11 11 0 0 0 4.6 7zm0 2h3a11 11 0 0 0 0 4.9A6.5 6.5 0 0 1 1.6 9zM8 14.5C7 13.3 6.3 11.5 6.1 9h3.8c-.2 2.5-.9 4.3-1.9 5.5zM11.4 7a11 11 0 0 0-1-4.9A6.5 6.5 0 0 1 14.4 7zm0 2h3a6.5 6.5 0 0 1-3 4.9 11 11 0 0 0 0-4.9z"/></svg>www.marloclean.com</li>
    </ul>
    <div class="brand back__brand">
      <span class="brand__dot"></span>
      <span class="brand__name">Marlo clean</span>
    </div>
  </div>
  <p class="address">210, 4th floor, Harbor Point<br>Road SDC</p>
  <div class="person">
    <p class="person__name">Dana Whitfield</p>
    <p class="person__title">Managing Director</p>
  </div>
</section>

</body>
</html>
```